Corvane Holdings , new business card design

investment firm with corporate clients . need double sided business card , vertical and horizontal options ,logo must be clear. prefer pantone colors only and sharp design. website also www.corvane.ae

Khalid Bin Tarrafi
Managing Director
Tel. +971 4 387 2940
Mobile +971 50 518 2403
khalid@corvane.ae
Q-Span Plaza, officw 18-B07, Warqa Gardens, Dubai

Contact Information for Business Card

Khalid Bin Tarrafi
Managing Director

Font styles to use
Serif

Colors

Designer to choose colors to be used in the design.

```html
<!DOCTYPE html>
<html lang="en">
<head>
<meta charset="utf-8">
<title>Corvane Holdings — Business Card</title>
<link rel="stylesheet" href="https://fonts.googleapis.com/css2?family=Josefin+Sans:wght@300&family=Lato:wght@400;700;900&display=swap">
<style>
  :root {
    --stage: #e9e7e3;
    --card-blue: #4a7199;
    --card-white: #ffffff;
    --wordmark-dark: #151a22;
    --wordmark-blue: #4a7199;
    --navy: #1c2a6b;
    --navy-soft: #2f4290;
    --text: #2a2f3a;
    --divider: #4a7199;
  }
  * { box-sizing: border-box; margin: 0; padding: 0; }
  html, body {
    width: 1200px; height: 960px; overflow: hidden;
    background: var(--stage);
  }
  .stage {
    width: 1200px; height: 960px;
    display: flex; flex-direction: column;
    align-items: center; justify-content: center; gap: 60px;
  }
  .card {
    width: 700px; height: 400px;
    position: relative;
    box-shadow: 0 6px 22px rgba(0,0,0,0.12);
  }
  .card--front {
    background: var(--card-blue);
    display: flex; flex-direction: column;
    align-items: center; justify-content: center;
  }
  .wordmark {
    display: flex; align-items: center; gap: 18px;
    font-family: "Josefin Sans", sans-serif; font-weight: 300;
    text-transform: uppercase;
  }
  .wordmark__square { width: 14px; height: 14px; background: currentColor; }
  .wordmark__text { display: flex; flex-direction: column; align-items: center; line-height: 1; }
  .wordmark__main { letter-spacing: 0.3em; margin-right: -0.3em; }
  .wordmark__sub { letter-spacing: 0.62em; margin-right: -0.62em; margin-top: 10px; }
  .card--front .wordmark { color: var(--wordmark-dark); }
  .card--front .wordmark__main { font-size: 56px; }
  .card--front .wordmark__sub { font-size: 19px; }
  .front-url {
    margin-top: 34px;
    font-family: "Lato", sans-serif; font-size: 22px;
    letter-spacing: 0.12em; color: #ffffff;
  }
  .card--back {
    background: var(--card-white);
    display: flex; align-items: center;
  }
  .back-logo {
    width: 345px; display: flex; justify-content: center;
  }
  .card--back .wordmark { color: var(--wordmark-blue); gap: 12px; }
  .card--back .wordmark__main { font-size: 36px; }
  .card--back .wordmark__sub { font-size: 12.5px; margin-top: 8px; }
  .back-divider {
    width: 2px; height: 240px; background: var(--divider);
  }
  .contact {
    padding-left: 34px;
    font-family: "Lato", sans-serif; color: var(--text);
  }
  .contact__name {
    font-weight: 900; font-size: 17px; color: var(--navy);
    text-transform: uppercase; letter-spacing: 0.02em;
  }
  .contact__role {
    font-size: 16px; color: var(--navy-soft);
    text-transform: uppercase; margin: 4px 0 18px 8px;
  }
  .contact__list { list-style: none; padding-left: 16px; }
  .contact__item {
    display: flex; align-items: flex-start; gap: 9px;
    font-size: 16px; line-height: 1.3; margin-bottom: 6px;
  }
  .contact__item--address { margin-top: 10px; }
  .contact__icon { width: 14px; height: 14px; margin-top: 3px; flex: none; fill: var(--navy); }
</style>
</head>
<body>
<main class="stage">
  <section class="card card--front" aria-label="Card front">
    <div class="wordmark">
      <span class="wordmark__square"></span>
      <span class="wordmark__text">
        <span class="wordmark__main">Corvane</span>
        <span class="wordmark__sub">Holdings</span>
      </span>
    </div>
    <p class="front-url">www.corvane.ae</p>
  </section>

  <section class="card card--back" aria-label="Card back">
    <div class="back-logo">
      <div class="wordmark">
        <span class="wordmark__square"></span>
        <span class="wordmark__text">
          <span class="wordmark__main">Corvane</span>
          <span class="wordmark__sub">Holdings</span>
        </span>
      </div>
    </div>
    <div class="back-divider"></div>
    <div class="contact">
      <p class="contact__name">Khalid Bin Tarrafi</p>
      <p class="contact__role">Managing Director</p>
      <ul class="contact__list">
        <li class="contact__item">
          <svg class="contact__icon" viewBox="0 0 24 24"><path d="M6.6 10.8a15 15 0 0 0 6.6 6.6l2.2-2.2a1 1 0 0 1 1-.25 11.4 11.4 0 0 0 3.6.57 1 1 0 0 1 1 1V20a1 1 0 0 1-1 1A17 17 0 0 1 3 4a1 1 0 0 1 1-1h3.5a1 1 0 0 1 1 1c0 1.25.2 2.45.57 3.57a1 1 0 0 1-.25 1z"/></svg>
          <span>+971 4 387 2940</span>
        </li>
        <li class="contact__item">
          <svg class="contact__icon" viewBox="0 0 24 24"><path d="M7 1h10a2 2 0 0 1 2 2v18a2 2 0 0 1-2 2H7a2 2 0 0 1-2-2V3a2 2 0 0 1 2-2zm0 3v14h10V4zm5 15.5a1.2 1.2 0 1 0 0 2.4 1.2 1.2 0 0 0 0-2.4z"/></svg>
          <span>+971 50 518 2403</span>
        </li>
        <li class="contact__item">
          <svg class="contact__icon" viewBox="0 0 24 24"><path d="M2 5h20v14H2zm2 2v.5l8 5 8-5V7zm0 2.9V17h16V9.9l-8 5z"/></svg>
          <span>khalid@corvane.ae</span>
        </li>
        <li class="contact__item">
          <svg class="contact__icon" viewBox="0 0 24 24"><path d="M12 2a10 10 0 1 0 0 20 10 10 0 0 0 0-20zm6.9 6h-3a15 15 0 0 0-1.3-3.9A8 8 0 0 1 18.9 8zM12 4.1c.8 1.1 1.5 2.4 1.9 3.9h-3.8c.4-1.5 1.1-2.8 1.9-3.9zM4.3 14a8 8 0 0 1 0-4h3.4a16 16 0 0 0 0 4zm.8 2h3a15 15 0 0 0 1.3 3.9A8 8 0 0 1 5.1 16zm3-8h-3a8 8 0 0 1 4.3-3.9A15 15 0 0 0 8.1 8zM12 19.9c-.8-1.1-1.5-2.4-1.9-3.9h3.8c-.4 1.5-1.1 2.8-1.9 3.9zm2.3-5.9H9.7a14 14 0 0 1 0-4h4.6a14 14 0 0 1 0 4zm.3 5.9a15 15 0 0 0 1.3-3.9h3a8 8 0 0 1-4.3 3.9zm1.7-5.9a16 16 0 0 0 0-4h3.4a8 8 0 0 1 0 4z"/></svg>
          <span>www.corvane.ae</span>
        </li>
        <li class="contact__item contact__item--address">
          <svg class="contact__icon" viewBox="0 0 24 24"><path d="M12 1a8 8 0 0 0-8 8c0 6 8 14 8 14s8-8 8-14a8 8 0 0 0-8-8zm0 11a3 3 0 1 1 0-6 3 3 0 0 1 0 6z"/></svg>
          <span>Q-Span Plaza, officw 18-B07<br>Warqa Gardens, Dubai</span>
        </li>
      </ul>
    </div>
  </section>
</main>
</body>
</html>
```